Fitness website

Website for a fitness brand (see attached specs). Design needs to be modern and vibrant with CTAs on every page. We will provide logos, images, etc but for now user placeholder text and images. For now use the name 'Corvane Athletics' as the name to use on the design. The goal of this site is to either get people to join the gym (5 physical locations across the US); buy an online program; buy merch or supplements or sign up for the newsletter. Pleas use images from this foldeR: https://filebarn.example/share/folders/8QwTz41mKpLrXv93NdYe7HsaBuJ0Cf2_R?usp=sharing

We will be coding this in ReactNative. Lots more work for the winner as well, this is a 1st project for us.

Target Market(s)

fitness enthusiats

Industry/Entity Type

fitness, health, wellness

Number of Pages Required

5+ page

Font styles to use
Other font styles liked:
• Lato

Colors
0054AA
0677BA
7BADD7
CADEEF
E8F1F8
0094D4
00A9DD
6FCCEA
C7EBF8
E9F6FB
00AB8E
00BBA5
67D7C9
C6EFE9
E9F9F6
EE7325
F08F49
F5BC92
FAE3D3
FDF4ED

Requirements
Must have
• must be reactive. most people will view it first on mobile
Nice to have
• video in hero section of top of home page

```html
<!DOCTYPE html>
<html lang="en">
<head>
<meta charset="utf-8">
<title>Corvane Athletics</title>
<link rel="stylesheet" href="https://fonts.googleapis.com/css2?family=Lato:wght@400;700;900&display=swap">
<style>
:root{
  --green:#1d7a35;
  --green-dark:#145c27;
  --ink:#111111;
  --dark:#161616;
  --gray:#e9e9e9;
  --muted:#555555;
  --white:#ffffff;
  --footer:#141414;
}
*{box-sizing:border-box;margin:0;padding:0}
html,body{width:1200px;height:4640px;overflow:hidden}
body{font-family:"Lato",Arial,sans-serif;color:var(--ink);background:var(--white);position:relative}
.abs{position:absolute}
.btn{display:inline-block;border-radius:40px;font-weight:700;font-size:15px;text-transform:uppercase;padding:14px 30px;letter-spacing:.5px}
.btn-green{background:var(--green);color:var(--white)}
.btn-dark{background:#0d0d0d;color:var(--white);border:2px solid #fff}
.section-title{font-weight:900;font-size:44px;text-align:center;letter-spacing:1px}
.title-rule{width:110px;height:5px;background:var(--green);margin:16px auto 0}

/* header & hero */
.hero{position:absolute;left:0;top:0;width:1200px;height:870px;background:linear-gradient(120deg,#3b3b3b 0%,#1f1f1f 45%,#4a4a4a 70%,#222 100%)}
.hero-shade{position:absolute;inset:0;background:rgba(0,0,0,.45)}
.site-header{position:absolute;left:0;top:0;width:1200px;height:72px;display:flex;align-items:center;padding:0 60px;background:rgba(0,0,0,.55)}
.brand{color:#fff;font-weight:900;font-size:28px;letter-spacing:.5px}
.main-nav{display:flex;gap:30px;margin-left:auto;color:#fff;font-size:14px;font-weight:700}
.main-nav .active{color:#fff;border-bottom:3px solid var(--green);padding-bottom:4px}
.nav-icons{display:flex;gap:20px;margin-left:34px}
.hero-copy{position:absolute;top:310px;left:0;width:1200px;text-align:center;color:#fff}
.hero-copy h1{font-weight:900;font-size:72px;letter-spacing:2px}
.hero-copy p{font-size:28px;font-weight:700;line-height:1.35;margin:14px auto 0;width:920px}
.hero-ctas{display:flex;justify-content:center;gap:30px;margin-top:52px}
.hero-ctas .btn{width:250px;text-align:center}
.play{margin-top:26px;font-size:15px;display:flex;justify-content:center;align-items:center;gap:8px}

/* about */
.about-photo{left:0;top:880px;width:560px;height:540px;background:linear-gradient(135deg,#6c6c6c,#2d2d2d)}
.about-copy{left:620px;top:950px;width:520px}
.about-copy h2{font-weight:900;font-size:44px;display:flex;align-items:center;gap:20px}
.about-copy h2 span{display:inline-block;width:90px;height:5px;background:var(--green)}
.about-copy p{font-size:16px;line-height:1.6;color:#333;margin-top:18px}

/* programs */
.programs{left:0;top:1500px;width:1200px;height:780px;background:var(--gray)}
.program-card{position:absolute;top:240px;width:288px;height:380px;background:linear-gradient(160deg,#5a5a5a,#1c1c1c);color:#fff;text-align:center}
.program-card h3{position:absolute;bottom:104px;left:0;width:100%;font-weight:900;font-size:30px;line-height:1.1}
.program-card .btn{position:absolute;bottom:34px;left:50%;transform:translateX(-50%);padding:12px 26px}
.dots{display:flex;gap:12px;justify-content:center}
.dots i{display:block;width:60px;height:4px;background:#1a1a1a}
.dots i.on{background:#1a1a1a;height:6px}

/* testimonials */
.testimonial{left:0;top:2330px;width:1200px;text-align:center}
.testimonial blockquote{font-style:italic;font-size:21px;line-height:1.5;color:#333;width:960px;margin:28px auto 0}
.testimonial .quote-mark{color:var(--green);font-size:34px;font-weight:900;margin-top:34px}
.testimonial .name{color:var(--green);font-weight:900;font-size:15px;margin-top:26px}

/* locations */
.locations{left:0;top:2700px;width:1200px;height:650px;background:linear-gradient(180deg,#2a2a2a,#111)}
.locations .section-title{color:#fff}
.loc-card{position:absolute;top:268px;width:242px;height:252px;background:linear-gradient(180deg,#8fb6d8,#3f6f8f)}
.loc-card.feature{border:6px solid var(--green)}
.loc-name{position:absolute;top:556px;width:242px;text-align:center;color:#fff;font-weight:900;font-size:22px}

/* blog */
.blog-head{left:72px;top:3488px;width:1060px;display:flex;justify-content:space-between;align-items:center}
.blog-head h2{font-weight:900;font-size:44px}
.post-main{left:72px;top:3600px;width:528px;height:228px;background:linear-gradient(135deg,#6d6d6d,#262626);color:#fff}
.post-main h4{position:absolute;left:28px;bottom:46px;font-weight:900;font-size:22px}
.post-main small,.post-side small{font-weight:700;font-size:14px;color:var(--green)}
.post-main small{position:absolute;left:28px;bottom:20px}
.post-thumb{left:612px;width:240px;height:100px;background:linear-gradient(135deg,#707070,#2b2b2b)}
.post-side{left:870px;width:262px}
.post-side h4{font-weight:900;font-size:20px;line-height:1.2;margin-bottom:6px}

/* newsletter & footer */
.footer{left:0;top:4120px;width:1200px;height:520px;background:var(--footer);color:#fff}
.newsletter{left:72px;top:4020px;width:1060px;height:156px;background:#f2f2f2;border-radius:6px;box-shadow:0 6px 18px rgba(0,0,0,.2);display:flex;align-items:center;padding:0 36px}
.newsletter h2{font-weight:900;font-size:44px;width:360px}
.news-field{position:relative;width:620px;height:56px;background:#fff;border:1px solid #ccc;border-radius:30px;display:flex;align-items:center;padding-left:26px;font-size:15px}
.news-field .btn{position:absolute;right:6px;top:5px;padding:13px 26px}
.foot-col{position:absolute;top:4250px}
.foot-col h5{font-weight:900;font-size:22px;margin-bottom:18px}
.foot-col p,.foot-col li{font-size:15px;line-height:1.75;color:#ddd;list-style:none}
.socials{display:flex;gap:12px;margin-top:16px}
.socials i{display:block;width:38px;height:38px;border-radius:50%;background:#fff}
.socials i.g{background:var(--green)}
.foot-bar{left:0;top:4560px;width:1200px;height:80px;border-top:1px solid #333;text-align:center;line-height:80px;font-size:14px;color:#bbb}
</style>
</head>
<body>

<section class="hero" role="img" aria-label="Hero video still of athletes training in a gym">
  <div class="hero-shade"></div>
</section>
<header class="site-header">
  <div class="brand">CORVANE ATHLETICS</div>
  <nav class="main-nav">
    <span class="active">HOME</span><span>ABOUT</span><span>PROGRAMS</span><span>SHOP</span><span>LOCATIONS</span><span>AFFILIATES</span><span>BLOGS</span><span>CONTACT</span>
  </nav>
  <div class="nav-icons">
    <svg width="18" height="18" viewBox="0 0 18 18"><circle cx="9" cy="6" r="4" fill="#fff"/><path d="M1 18c0-5 4-7 8-7s8 2 8 7z" fill="#fff"/></svg>
    <svg width="18" height="18" viewBox="0 0 18 18"><circle cx="7.5" cy="7.5" r="5.5" fill="none" stroke="#fff" stroke-width="2.5"/><path d="M11.5 11.5L17 17" stroke="#fff" stroke-width="2.5"/></svg>
  </div>
</header>
<div class="hero-copy">
  <h1>CORVANE ATHLETICS</h1>
  <p>Nemo enim ipsam voluptatem quia voluptas sit aspernatur aut odit aut fugit, sed quia consequuntur magni dolores.</p>
  <div class="hero-ctas">
    <span class="btn btn-green">Buy an online program</span>
    <span class="btn btn-dark">Join the gym</span>
  </div>
  <div class="play">
    <svg width="18" height="18" viewBox="0 0 18 18"><circle cx="9" cy="9" r="8" fill="none" stroke="#fff" stroke-width="1.6"/><path d="M7 5.5l5 3.5-5 3.5z" fill="#fff"/></svg>
    PLAY VIDEO
  </div>
</div>
<svg class="abs" style="left:0;top:740px" width="1200" height="140" viewBox="0 0 1200 140">
  <path d="M0 110 L700 40 L1200 80 L1200 140 L0 140Z" fill="#fff"/>
  <path d="M880 55 L1200 20 L1200 95 Z" fill="var(--green)"/>
</svg>

<div class="abs about-photo" role="img" aria-label="Photo of athletes lifting barbells in a gym"></div>
<svg class="abs" style="left:440px;top:880px" width="140" height="540" viewBox="0 0 140 540">
  <path d="M60 0 L140 0 L140 540 L0 540Z" fill="#fff"/>
  <path d="M96 0 L60 0 L0 540 L28 540Z" fill="var(--green)" opacity="0"/>
</svg>
<svg class="abs" style="left:540px;top:1000px" width="40" height="420" viewBox="0 0 40 420"><path d="M40 0 L40 420 L0 420Z" fill="var(--green)"/></svg>
<div class="abs about-copy">
  <h2>ABOUT <span></span></h2>
  <p>Nemo enim ipsam voluptatem quia voluptas sit aspernatur aut odit aut fugit, sed quia consequuntur magni dolores eos qui ratione voluptatem sequi nesciunt. Neque porro quisquam est, qui dolorem ipsum quia dolor sit amet, consectetur, adipisci velit, sed quia non numquam eius modi tempora incidunt ut labore et dolore magnam.</p>
  <p>Nemo enim ipsam voluptatem quia voluptas sit aspernatur aut odit aut fugit, sed quia consequuntur magni dolores eos qui ratione voluptatem sequi nesciunt. Neque porro quisquam est.</p>
  <span class="btn btn-green" style="margin-top:26px">Learn more</span>
</div>

<section class="abs programs">
  <svg class="abs" style="left:0;top:-40px" width="1200" height="110" viewBox="0 0 1200 110">
    <path d="M0 20 L520 70 L0 70Z" fill="var(--green)"/>
    <path d="M0 40 L600 110 L1200 50 L1200 110 L0 110Z" fill="var(--gray)"/>
    <path d="M760 80 L1200 30 L1200 50 Z" fill="var(--green)"/>
  </svg>
  <div class="abs" style="left:0;top:120px;width:1200px">
    <h2 class="section-title">OUR PROGRAMS</h2>
    <div class="title-rule"></div>
  </div>
  <div class="program-card" style="left:0" role="img" aria-label="Masters program photo"><h3>MASTERS</h3><span class="btn btn-green">Learn more</span></div>
  <div class="program-card" style="left:304px" role="img" aria-label="Functional fitness program photo"><h3>FUNCTIONAL<br>FITNESS</h3><span class="btn btn-green">Learn more</span></div>
  <div class="program-card" style="left:608px" role="img" aria-label="Competitive program photo"><h3>COMPETITIVE</h3><span class="btn btn-green">Learn more</span></div>
  <div class="program-card" style="left:912px" role="img" aria-label="Nutrition program photo"><h3>NUTRITIONS</h3><span class="btn btn-green">Learn more</span></div>
  <div class="dots abs" style="left:0;top:690px;width:1200px"><i class="on"></i><i></i><i></i></div>
</section>

<section class="abs testimonial">
  <h2 class="section-title">TESTIMONIALS</h2>
  <div class="title-rule"></div>
  <blockquote>“ Nemo enim ipsam voluptatem quia voluptas sit aspernatur aut odit aut fugit, sed quia consequuntur magni dolores eos qui ratione voluptatem sequi nesciunt porro quisquam est, qui dolorem ipsum quia dolor sit amet, consectetur..”</blockquote>
  <div class="name">NAME HEADING</div>
  <div class="dots" style="margin-top:60px"><i class="on"></i><i></i><i></i></div>
</section>

<section class="abs locations" role="region" aria-label="Our locations">
  <svg class="abs" style="left:0;top:0" width="1200" height="90" viewBox="0 0 1200 90">
    <path d="M0 0 L1200 0 L1200 10 L0 50Z" fill="#fff"/>
    <path d="M700 60 L1200 10 L1200 50 Z" fill="var(--green)"/>
  </svg>
  <div class="abs" style="left:0;top:160px;width:1200px">
    <h2 class="section-title">OUR LOCATIONS</h2>
    <div class="title-rule"></div>
  </div>
  <svg class="abs" style="left:140px;top:378px" width="24" height="36" viewBox="0 0 24 36"><path d="M20 2 L4 18 L20 34" fill="none" stroke="#fff" stroke-width="4"/></svg>
  <svg class="abs" style="left:1036px;top:378px" width="24" height="36" viewBox="0 0 24 36"><path d="M4 2 L20 18 L4 34" fill="none" stroke="#fff" stroke-width="4"/></svg>
  <div class="loc-card" style="left:208px" role="img" aria-label="San Diego skyline photo"></div>
  <div class="loc-card feature" style="left:479px" role="img" aria-label="Boston skyline photo"></div>
  <div class="loc-card" style="left:750px;background:linear-gradient(180deg,#c9895a,#3d4f6a)" role="img" aria-label="Miami skyline photo"></div>
  <div class="loc-name" style="left:208px">SAN DIEGO</div>
  <div class="loc-name" style="left:479px">BOSTON</div>
  <div class="loc-name" style="left:750px">MIAMI</div>
  <svg class="abs" style="left:0;top:560px" width="1200" height="90" viewBox="0 0 1200 90">
    <path d="M0 90 L0 50 L600 80 L1200 30 L1200 90Z" fill="#fff"/>
    <path d="M0 30 L420 68 L0 50Z" fill="var(--green)"/>
  </svg>
</section>

<div class="abs blog-head">
  <h2>BLOG POSTS</h2>
  <span class="btn btn-green">View all</span>
</div>
<div class="abs post-main" role="img" aria-label="Blog post photo of athletes training">
  <h4>NEMO ENIM IPSAM VOLUPTA</h4>
  <small>OCTOBER 25, 2025</small>
</div>
<div class="abs post-thumb" style="top:3600px" role="img" aria-label="Blog post photo of a workout"></div>
<div class="abs post-side" style="top:3610px"><h4>NEMO ENIM IPSAM VOLU PTATEM RATIONE VOLUPTA TEM SEQUI</h4><small>AUGUST 25, 2025</small></div>
<div class="abs post-thumb" style="top:3722px" role="img" aria-label="Blog post photo of a gym session"></div>
<div class="abs post-side" style="top:3732px"><h4>NEMO ENIM IPSAM VOLU PTATEM RATIONE VOLUPTA TEM SEQUI</h4><small>AUGUST 25, 2025</small></div>

<footer class="abs footer"></footer>
<div class="abs newsletter">
  <h2>NEWSLETTER</h2>
  <div class="news-field">Email Address<span class="btn btn-green">Subscribe</span></div>
</div>

<div class="foot-col" style="left:72px;width:330px">
  <h5>CORVANE ATHLETICS</h5>
  <p>Excepteur sint occaecat cupidatat non proident, sunt in culpa qui officia deserunt mollit anim id est laborum.</p>
  <p style="margin-top:14px">Enim ipsam voluptatem quia voluptas sit aspernatur aut odit aut fugit, sed quia consequuntur magni dolores.</p>
</div>
<div class="foot-col" style="left:460px">
  <h5>NAVIGATIONS</h5>
  <ul><li>Home</li><li>About</li><li>Programs</li><li>Shop</li><li>Locations</li><li>Affiliates</li><li>Blog</li><li>Contact</li></ul>
</div>
<div class="foot-col" style="left:680px">
  <h5>ABOUT US</h5>
  <ul><li>Brands</li><li>Gyms</li><li>Coaches</li><li>Owner</li><li>Advisor Team</li></ul>
</div>
<div class="foot-col" style="left:880px;width:260px">
  <h5>CONTACT INFO</h5>
  <p>418 Harlow Street Suite 12,<br>Denver 80204, United States</p>
  <p style="margin-top:8px">+1 555-014-2277</p>
  <p>hello@corvanemail.test</p>
  <div class="socials"><i class="g"></i><i></i><i></i><i></i></div>
</div>
<div class="abs foot-bar">©2025 Corvane Athletics | All Right Reserved | Privacy Policy</div>

</body>
</html>
```